Business Card Design

We are a manufacturing and distribution company with most of our customer base being supermarkets. We have established brand guidelines that are attached.

```html
<!DOCTYPE html>
<html lang="en">
<head>
<meta charset="utf-8">
<title>Valorin Business Card</title>
<link href="https://fonts.googleapis.com/css2?family=Montserrat:wght@800&family=Arimo:wght@400;700&display=swap" rel="stylesheet">
<style>
  :root {
    --canvas-bg: #e6e6e4;
    --card-white: #ffffff;
    --brand-red: #e21b23;
    --brand-blue: #0566ac;
    --ink-black: #1a1a1a;
    --ink-grey: #6b6b6b;
    --wordmark-white: #ffffff;
  }
  * { box-sizing: border-box; margin: 0; padding: 0; }
  html, body {
    width: 1200px;
    height: 802px;
    overflow: hidden;
    background: var(--canvas-bg);
  }
  .canvas {
    width: 1200px;
    height: 802px;
    display: flex;
    align-items: center;
    justify-content: center;
    gap: 60px;
  }
  .card {
    width: 520px;
    height: 298px;
    position: relative;
    overflow: hidden;
    border-bottom: 4px solid var(--brand-red);
    box-shadow: 0 12px 28px rgba(0, 0, 0, 0.16);
  }

  /* Front */
  .card-front {
    background: var(--card-white);
    padding: 42px 40px;
    font-family: "Arimo", Arial, sans-serif;
  }
  .company-name {
    display: flex;
    align-items: center;
    gap: 10px;
    font-family: "Montserrat", Arial, sans-serif;
    font-weight: 800;
    font-size: 26px;
    letter-spacing: 1.5px;
    color: var(--ink-black);
  }
  .company-mark {
    width: 18px;
    height: 18px;
    background: var(--brand-red);
  }
  .person {
    margin-top: 24px;
  }
  .person-name {
    font-size: 15px;
    font-weight: 700;
    color: var(--brand-red);
    text-transform: uppercase;
    letter-spacing: 0.4px;
  }
  .person-title {
    font-size: 13px;
    color: var(--ink-grey);
    margin-top: 2px;
  }
  .address {
    margin-top: 16px;
    font-size: 13px;
    line-height: 1.35;
    color: var(--ink-grey);
  }
  .contact-list {
    list-style: none;
    margin-top: 14px;
    font-size: 13px;
    line-height: 1.45;
    color: var(--ink-grey);
  }
  .contact-list li {
    display: flex;
    align-items: center;
    gap: 8px;
  }
  .contact-icon {
    width: 11px;
    height: 11px;
    flex: none;
  }

  /* Back */
  .card-back {
    background: var(--brand-blue);
    display: flex;
    align-items: center;
    justify-content: center;
  }
  .back-wordmark {
    font-family: "Montserrat", Arial, sans-serif;
    font-weight: 800;
    font-size: 42px;
    letter-spacing: 3px;
    color: var(--wordmark-white);
  }
</style>
</head>
<body>
<main class="canvas">

  <section class="card card-front" aria-label="Business card front">
    <div class="company-name"><span class="company-mark"></span>VALORIN</div>

    <div class="person">
      <p class="person-name">Daniel Reyes</p>
      <p class="person-title">Manager</p>
    </div>

    <p class="address">Your address, city<br>state, ZIP 0000</p>

    <ul class="contact-list">
      <li>
        <svg class="contact-icon" viewBox="0 0 12 12" aria-hidden="true">
          <path d="M3 1 L5 3.5 L4 5 Q5 7 7 8 L8.5 7 L11 9 L10 11 Q5 11 1 2 Z" fill="#e21b23"/>
        </svg>
        555-318-0742
      </li>
      <li>
        <svg class="contact-icon" viewBox="0 0 12 12" aria-hidden="true">
          <rect x="0.8" y="2.3" width="10.4" height="7.4" fill="none" stroke="#e21b23" stroke-width="1.2"/>
          <path d="M1 2.6 L6 6.6 L11 2.6" fill="none" stroke="#e21b23" stroke-width="1.2"/>
        </svg>
        youremail@mailbox.com
      </li>
      <li>
        <svg class="contact-icon" viewBox="0 0 12 12" aria-hidden="true">
          <circle cx="6" cy="6" r="5" fill="none" stroke="#e21b23" stroke-width="1.2"/>
          <ellipse cx="6" cy="6" rx="2.2" ry="5" fill="none" stroke="#e21b23" stroke-width="1"/>
          <path d="M1 6 H11" stroke="#e21b23" stroke-width="1"/>
        </svg>
        www.yourwebsite.com
      </li>
    </ul>
  </section>

  <section class="card card-back" aria-label="Business card back">
    <p class="back-wordmark">VALORIN</p>
  </section>

</main>
</body>
</html>
```